Business cards and stationary design

We just completed the design of our new logo and we need to print new business cards and letterhead for our nonprofit. We are looking for a fresh new design that shows off our new logo. On letterhead, we must have a column on the right or left to include our Board of Directors (up to 45 names) (see attachment)

Industry/Entity Type

Non-Profit

Contact Information for Business Card

Standard business card with name, title, Company name, mailing address phone numbers, email address and website. Tagline on back "Bringing the homeless home"

Font styles to use
Sans Serif

Requirements
Must have
• include pertinent information above
• new logo
• fonts compatible with logo
• should use logo colors only
Nice to have
• tag lines

```html
<!DOCTYPE html>
<html lang="en">
<head>
<meta charset="utf-8">
<title>Homeward Shelter Alliance – Business Card</title>
<link href="https://fonts.googleapis.com/css2?family=Michroma&family=Arimo:wght@400;600&display=swap" rel="stylesheet">
<style>
  :root {
    --bg: #e4e4e4;
    --card: #f8f8f8;
    --card-back: #f2f2f2;
    --teal: #1a8aa6;
    --gold: #f6b824;
    --red: #dc2128;
    --ink: #555555;
    --ink-soft: #666666;
  }
  * { margin: 0; padding: 0; box-sizing: border-box; }
  html, body { width: 1200px; height: 582px; overflow: hidden; }
  body {
    background: var(--bg);
    position: relative;
    font-family: "Arimo", sans-serif;
  }
  .card {
    position: absolute;
    top: 158px;
    width: 464px;
    height: 264px;
    overflow: hidden;
  }
  .card--front { left: 122px; background: var(--card); }
  .card--back { left: 602px; background: var(--card-back); }

  .brand {
    position: absolute;
    left: 30px;
    top: 96px;
    width: 200px;
    text-align: center;
  }
  .brand__mark {
    display: block;
    width: 14px;
    height: 14px;
    border-radius: 50%;
    background: var(--teal);
    margin: 0 auto 10px;
  }
  .brand__name {
    font-family: "Arimo", sans-serif;
    font-weight: 600;
    color: var(--teal);
    font-size: 14px;
    letter-spacing: 1.5px;
    line-height: 1.25;
  }
  .brand__rule {
    height: 1px;
    background: var(--red);
    opacity: .7;
    margin-top: 8px;
  }

  .details {
    position: absolute;
    left: 260px;
    top: 58px;
    color: var(--ink);
  }
  .details__name {
    font-family: "Michroma", sans-serif;
    color: var(--red);
    font-size: 15px;
    letter-spacing: 1px;
    line-height: 18px;
  }
  .details__title {
    font-family: "Michroma", sans-serif;
    color: var(--gold);
    font-size: 8px;
    letter-spacing: 1px;
    margin-bottom: 10px;
  }
  .details__address { font-size: 11px; line-height: 13.5px; margin-bottom: 8px; }
  .contact { list-style: none; font-size: 10.5px; }
  .contact li { display: flex; align-items: center; gap: 6px; height: 15px; }
  .contact li:first-child { font-size: 11.5px; }
  .contact svg { width: 10px; height: 10px; flex: none; }

  .band { position: absolute; left: 0; }
  .band--teal { top: 246px; height: 6px; width: 402px; background: var(--teal); }
  .band--red { top: 246px; height: 6px; left: 426px; width: 38px; background: var(--red); }
  .band--gold { top: 254px; height: 10px; width: 464px; background: var(--gold); }

  .back-brand {
    position: absolute;
    left: 0; right: 0;
    top: 96px;
    text-align: center;
  }
  .back-brand__mark {
    display: block;
    width: 22px; height: 22px;
    border-radius: 50%;
    background: var(--teal);
    margin: 0 auto 12px;
  }
  .back-brand__name {
    font-family: "Arimo", sans-serif;
    font-weight: 600;
    color: var(--teal);
    font-size: 20px;
    letter-spacing: 2px;
  }
  .tagline {
    position: absolute;
    left: 0; right: 0;
    top: 219px;
    text-align: center;
    font-family: "Michroma", sans-serif;
    font-size: 11px;
    letter-spacing: .5px;
    color: var(--ink-soft);
  }
</style>
</head>
<body>
  <section class="card card--front" aria-label="Business card front">
    <div class="brand">
      <span class="brand__mark"></span>
      <div class="brand__name">HOMEWARD SHELTER ALLIANCE</div>
      <div class="brand__rule"></div>
    </div>

    <div class="details">
      <div class="details__name">DANA WHITFIELD</div>
      <div class="details__title">CEO/FOUNDER</div>
      <p class="details__address">Homeward Shelter Alliance<br>2140 Birchwood Road<br>Fairbanks, Alaska 99701</p>
      <ul class="contact">
        <li>
          <svg viewBox="0 0 10 10" aria-hidden="true"><path fill="#dc2128" d="M2 0.5 L3.6 2.6 L2.7 3.6 Q3.8 5.9 6.4 7.3 L7.4 6.4 L9.5 8 L8.3 9.5 Q2.5 8.6 0.5 1.7 Z"/></svg>
          555 310 4821
        </li>
        <li>
          <svg viewBox="0 0 10 10" aria-hidden="true"><rect x="0.5" y="2" width="9" height="6.5" fill="#dc2128"/><path d="M0.8 2.3 L5 5.6 L9.2 2.3" stroke="#f8f8f8" stroke-width="0.9" fill="none"/></svg>
          dana@homewardalliance.org
        </li>
        <li>
          <svg viewBox="0 0 10 10" aria-hidden="true"><circle cx="5" cy="5" r="4.6" fill="#dc2128"/><path d="M2.5 3 Q4 2.5 4.5 4 Q3.5 5.5 4.5 7.5 M6 2 Q7.5 4 6.5 5.5" stroke="#f8f8f8" stroke-width="0.9" fill="none"/></svg>
          www.homewardalliance.org
        </li>
      </ul>
    </div>

    <div class="band band--teal"></div>
    <div class="band band--red"></div>
    <div class="band band--gold"></div>
  </section>

  <section class="card card--back" aria-label="Business card back">
    <div class="back-brand">
      <span class="back-brand__mark"></span>
      <div class="back-brand__name">HOMEWARD SHELTER ALLIANCE</div>
    </div>
    <p class="tagline">Your Tagline Here</p>
  </section>
</body>
</html>
```